Business Card Design for Training Business

Clear Path Coaching is a new business that delivers training and other services with a focus on topics related to mental health and wellbeing, for example, Wellmind Response Course, Resilience etc. We have a strong focus on evidence-based psychology and neuroscience. I have a logo which I will upload with the brief, so please consider colours that work well with the logo.
Target Market(s)
Adults, workplaces (particularly government and not-for-profits)
Industry/Entity Type
Business
Contact Information for Business Card
Head Strong TrainingSamantha SellwoodDirector0438 770 850sam@headstrongtraining.com.auwww.headstrongtraining.com.au

```html
<!DOCTYPE html>
<html lang="en">
<head>
<meta charset="utf-8">
<title>Clear Path Coaching — Business Card</title>
<link rel="stylesheet" href="https://fonts.googleapis.com/css2?family=Source+Sans+3:wght@400;600&display=swap">
<style>
  :root {
    --page-bg: #e9e6e1;
    --teal-deep: #0d8587;
    --teal-light: #2fa2a4;
    --card-white: #ffffff;
    --wordmark: #8b807a;
    --mark-ring: #6cc0c0;
    --ink: #1d1d1d;
  }
  * { margin: 0; padding: 0; box-sizing: border-box; }
  html, body {
    width: 1200px;
    height: 800px;
    overflow: hidden;
    background: var(--page-bg);
    font-family: "Source Sans 3", sans-serif;
  }
  .card {
    position: absolute;
    left: 75px;
    top: 100px;
    width: 1050px;
    height: 600px;
    overflow: hidden;
    box-shadow: 0 6px 24px rgba(0,0,0,0.18);
  }
  .card-backdrop {
    position: absolute;
    inset: 0;
    width: 100%;
    height: 100%;
  }
  .card-content {
    position: absolute;
    left: 150px;
    right: 90px;
    top: 0;
    bottom: 0;
    text-align: center;
  }
  .brand {
    position: absolute;
    left: 0;
    right: 0;
    top: 70px;
  }
  .brand-mark {
    display: block;
    width: 108px;
    height: 108px;
    margin: 0 auto 22px;
    border-radius: 50%;
    border: 3px solid var(--mark-ring);
  }
  .brand-name {
    font-weight: 400;
    font-size: 40px;
    letter-spacing: 0.14em;
    text-transform: uppercase;
    color: var(--wordmark);
  }
  .person {
    position: absolute;
    left: 0;
    right: 0;
    top: 290px;
  }
  .person-name {
    font-weight: 400;
    font-size: 46px;
    color: var(--teal-deep);
    line-height: 1.1;
  }
  .person-role {
    font-size: 26px;
    color: var(--ink);
    margin-top: 6px;
  }
  .contact {
    position: absolute;
    left: 0;
    right: 0;
    top: 420px;
    list-style: none;
    font-size: 27px;
    line-height: 1.35;
    color: var(--ink);
  }
</style>
</head>
<body>
  <article class="card">
    <svg class="card-backdrop" viewBox="0 0 1050 600" preserveAspectRatio="none" aria-hidden="true">
      <defs>
        <linearGradient id="teal-field" x1="0" y1="0" x2="1" y2="1">
          <stop offset="0" stop-color="#0d8587"/>
          <stop offset="1" stop-color="#2fa2a4"/>
        </linearGradient>
      </defs>
      <rect width="1050" height="600" fill="url(#teal-field)"/>
      <ellipse cx="585" cy="300" rx="455" ry="400" fill="#ffffff"/>
    </svg>

    <div class="card-content">
      <header class="brand">
        <span class="brand-mark"></span>
        <h1 class="brand-name">Clear Path Coaching</h1>
      </header>

      <section class="person">
        <h2 class="person-name">Rebecca Tanfield</h2>
        <p class="person-role">Director</p>
      </section>

      <ul class="contact">
        <li class="contact-phone">0491 362 517</li>
        <li class="contact-email">bec@clearpathcoaching.example.au</li>
        <li class="contact-web">www.clearpathcoaching.example.au</li>
      </ul>
    </div>
  </article>
</body>
</html>
```